Young Architect Bussiness Card

English is not my first language (spanish is).
Need a bussiness card design for my best friend who is about to graduate from college, Licentiate degree in architecture, so she needs business cards to start networking, currently she has no porfolio, web page or plazared. so she is relying on her cel phone and correovela, but should leave space for one of them (plazared)

Design for business card should be modern, maybe something with construction blue prints patern or 3D modelling.

Name: Mariela Otárola Bonilla
Licentiate in Arquitecture
Cel: (506) XXX-4827
email: marielaXXX@correovela.com

Services, although im not sure if it has to be there or not:
Anteproyectos / Proposal design
Inspecciones / Site Inspections
Modelado 3D / 3D modelling
Planos Constructivos / Construction Blue Prints
Presupuestos / Budgets

Design should be in spanish

Industry/Entity Type

Architect

Contact Information for Business Card

Name: Mariela Otárola, Arquitecto
Associtation code : XXXX
Phone: (506) XXXX-XXXX
Email: xxx@correovela.com
Plazared: xxxx

Requirements
Must have
• Design for business card should be modern, maybe something with construction blue prints patern or 3D modelling.
Nice to have
• Something like a transition from 2D to 3D.

```html
<!DOCTYPE html>
<html lang="es">
<head>
<meta charset="utf-8">
<title>Mariela Otárola Bonilla – Business Card</title>
<link rel="stylesheet" href="https://fonts.googleapis.com/css2?family=Cormorant+Garamond:ital,wght@1,600&family=Source+Sans+3:wght@400&family=Arimo:wght@700&display=swap">
<style>
  :root {
    --backdrop: #d4d4d4;
    --paper: #ffffff;
    --plum: #77375a;
    --rose: #d05a8e;
    --rose-text: #d0609a;
    --plum-text: #6e3656;
    --ink: #111111;
    --photo-yellow: #f1d35a;
    --photo-pale: #e8edf3;
    --photo-blue: #cdd8e5;
  }
  * { margin: 0; padding: 0; box-sizing: border-box; }
  html, body {
    width: 1189px; height: 1200px; overflow: hidden;
    background: var(--backdrop);
  }
  .card {
    position: absolute; left: 194px;
    width: 808px; height: 460px;
    overflow: hidden;
  }
  .card--front { top: 111px; background: var(--paper); }
  .card--back { top: 620px; }

  .front-bands { position: absolute; inset: 0; }

  .holder-name {
    position: absolute; right: 70px; top: 64px;
    font-family: "Cormorant Garamond", serif;
    font-style: italic; font-weight: 600;
    font-size: 52px; line-height: 1; letter-spacing: 1.5px;
    color: var(--rose-text); white-space: nowrap;
  }
  .holder-title {
    position: absolute; left: 487px; top: 134px;
    font-family: "Source Sans 3", sans-serif;
    font-size: 19px; line-height: 26px; color: var(--plum-text);
    white-space: nowrap;
  }

  .services {
    position: absolute; left: 30px; top: 262px;
    list-style: none;
    font-family: "Source Sans 3", sans-serif;
    font-size: 18px; color: var(--paper);
  }
  .services li {
    display: flex; align-items: center; gap: 14px;
    height: 37.7px; white-space: nowrap;
  }
  .services .star { width: 18px; height: 18px; fill: var(--rose); flex: none; }

  .contact {
    position: absolute; right: 88px; top: 305px;
    list-style: none; text-align: right;
    font-family: "Source Sans 3", sans-serif;
    font-size: 18px; line-height: 37px; color: var(--paper);
  }
  .contact li { height: 37px; white-space: nowrap; }

  .back-photo {
    position: absolute; inset: 0;
    background: linear-gradient(135deg, var(--photo-yellow) 0%, var(--photo-pale) 45%, var(--photo-blue) 100%);
  }
  .back-name {
    position: absolute; right: 39px; top: 382px;
    font-family: "Arimo", sans-serif; font-weight: 700;
    font-size: 40px; line-height: 46px; color: var(--ink); white-space: nowrap;
  }
</style>
</head>
<body>

<section class="card card--front">
  <svg class="front-bands" viewBox="0 0 808 460" aria-hidden="true">
    <polygon points="0,234 328,234 476,460 0,460" fill="var(--plum)"/>
    <polygon points="337,234 808,237 808,460 484,460" fill="var(--paper)"/>
    <polygon points="345,234 808,237 808,460 492,460" fill="var(--rose)"/>
  </svg>

  <h1 class="holder-name">Mariela Otárola Bonilla</h1>
  <p class="holder-title">Licentiate in Arquitecture</p>

  <ul class="services">
    <li><svg class="star" viewBox="0 0 24 24"><polygon points="12,1 15,9 23,9 16.5,14 19,22 12,17 5,22 7.5,14 1,9 9,9"/></svg>Anteproyectos / Proposal design</li>
    <li><svg class="star" viewBox="0 0 24 24"><polygon points="12,1 15,9 23,9 16.5,14 19,22 12,17 5,22 7.5,14 1,9 9,9"/></svg>Inspecciones / Site Inspections</li>
    <li><svg class="star" viewBox="0 0 24 24"><polygon points="12,1 15,9 23,9 16.5,14 19,22 12,17 5,22 7.5,14 1,9 9,9"/></svg>Modelado 3D / 3D modelling</li>
    <li><svg class="star" viewBox="0 0 24 24"><polygon points="12,1 15,9 23,9 16.5,14 19,22 12,17 5,22 7.5,14 1,9 9,9"/></svg>Planos Constructivos / Construction Blue Prints</li>
    <li><svg class="star" viewBox="0 0 24 24"><polygon points="12,1 15,9 23,9 16.5,14 19,22 12,17 5,22 7.5,14 1,9 9,9"/></svg>Presupuestos / Budgets</li>
  </ul>

  <ul class="contact">
    <li>(506) XXX-4827</li>
    <li>marielaXXX@correovela.com</li>
    <li>Associtation code : XXXX</li>
    <li>Plazared: xxxx</li>
  </ul>
</section>

<section class="card card--back">
  <div class="back-photo" role="img" aria-label="Photo placeholder: yellow hard hat, rolled blueprints, folding ruler, spirit level and tape measure on architectural plans"></div>
  <p class="back-name">MARIELA OTÁROLA BONILLA</p>
</section>

</body>
</html>
```